Business card design for my company.
I would like the card's background colour to be black. You can also see our web site to get an idea of our brand. https://www.tmwhomecrafting.com.au/
- Name
- Email

```html
<!DOCTYPE html>
<html lang="en">
<head>
<meta charset="utf-8">
<title>TMW Home Crafting – Business Card</title>
<link href="https://fonts.googleapis.com/css2?family=Montserrat:wght@400;500;700&display=swap" rel="stylesheet">
<style>
  :root {
    --stage: #3a3a3a;
    --card: #121212;
    --green: #1c9444;
    --white: #f2f2f2;
    --emboss: #2c2c2c;
  }
  * { box-sizing: border-box; margin: 0; padding: 0; }
  html, body { width: 1200px; height: 694px; overflow: hidden; }
  body {
    background: var(--stage);
    font-family: "Montserrat", Arial, sans-serif;
    position: relative;
  }
  .card {
    position: absolute;
    top: 197px;
    width: 520px;
    height: 300px;
    background: var(--card);
    border-radius: 18px;
  }
  .card-front { left: 50px; }
  .card-back { left: 630px; }

  .front-brand {
    position: absolute;
    inset: 0;
    display: flex;
    align-items: center;
    justify-content: center;
    gap: 14px;
  }
  .front-brand .brand-dot {
    width: 22px; height: 22px; border-radius: 50%;
    background: var(--emboss);
  }
  .front-brand .brand-name {
    font-size: 34px; font-weight: 700; letter-spacing: 2px;
    color: var(--emboss);
  }

  .back-brand {
    position: absolute;
    left: 34px; top: 110px;
    width: 190px;
    display: flex;
    align-items: center;
    gap: 10px;
  }
  .back-brand .brand-dot {
    flex: none;
    width: 16px; height: 16px; border-radius: 50%;
    background: var(--green);
  }
  .back-brand .brand-name {
    font-size: 22px; font-weight: 700; line-height: 1.15;
    color: var(--white);
  }

  .divider {
    position: absolute;
    left: 238px; top: 60px;
    width: 2px; height: 180px;
    background: var(--green);
  }

  .contact {
    position: absolute;
    left: 262px; top: 62px;
    color: var(--white);
  }
  .contact .person-name {
    font-size: 24px; font-weight: 700; color: var(--green);
    line-height: 1.1;
  }
  .contact .person-role {
    font-size: 13px; font-weight: 500; margin-top: 4px;
  }
  .contact-list { list-style: none; margin-top: 22px; }
  .contact-list li {
    display: flex; align-items: center; gap: 9px;
    font-size: 11.5px; font-weight: 500;
    margin-bottom: 11px;
  }
  .contact-list .icon {
    flex: none;
    width: 18px; height: 18px; border-radius: 50%;
    background: var(--green);
    display: flex; align-items: center; justify-content: center;
  }
  .contact-list svg { width: 10px; height: 10px; }
</style>
</head>
<body>
  <section class="card card-front" aria-label="Card front">
    <div class="front-brand">
      <span class="brand-dot"></span>
      <span class="brand-name">TMW Home Crafting</span>
    </div>
  </section>

  <section class="card card-back" aria-label="Card back">
    <div class="back-brand">
      <span class="brand-dot"></span>
      <span class="brand-name">TMW Home Crafting</span>
    </div>
    <div class="divider"></div>
    <div class="contact">
      <p class="person-name">Liam Hartley</p>
      <p class="person-role">General Manager</p>
      <ul class="contact-list">
        <li><span class="icon"><svg viewBox="0 0 10 10"><path d="M5 0.5a3 3 0 0 1 3 3c0 2.2-3 6-3 6s-3-3.8-3-6a3 3 0 0 1 3-3z" fill="#fff"/><circle cx="5" cy="3.5" r="1.1" fill="#1c9444"/></svg></span>Devonport, Tasmania, Australia</li>
        <li><span class="icon"><svg viewBox="0 0 10 10"><path d="M2.2 0.8l1.6 1.8-1 1.2c.7 1.4 1.8 2.5 3.2 3.2l1.2-1 1.8 1.6-1 1.6C4.6 9 1 5.4.8 1.8z" fill="#fff"/></svg></span>0400 555 017</li>
        <li><span class="icon"><svg viewBox="0 0 10 10"><rect x="0.8" y="2" width="8.4" height="6" fill="#fff"/><path d="M0.8 2l4.2 3.4L9.2 2" fill="none" stroke="#1c9444" stroke-width="0.9"/></svg></span>info@tmwhomecrafting.com.au</li>
        <li><span class="icon"><svg viewBox="0 0 10 10"><circle cx="5" cy="5" r="4.2" fill="none" stroke="#fff" stroke-width="1"/><ellipse cx="5" cy="5" rx="1.8" ry="4.2" fill="none" stroke="#fff" stroke-width="0.8"/><path d="M0.8 5h8.4" stroke="#fff" stroke-width="0.8"/></svg></span>www.tmwhomecrafting.com.au</li>
      </ul>
    </div>
  </section>
</body>
</html>
```